Rosko Tamblin

I am a songwriter and would like to include a bio, pictures, discography, CD covers and access to some of my music

Target Market(s)

Music Lovers, songwriters publishers

Coding

Coded - Design and coding required

Number of Pages Required

5+ page

Requirements
Must have
• Pictures of my CD covers, pictures of me and either my Music or links to my music
Nice to have
Should not have
• cartoons

```html
<!DOCTYPE html>
<html lang="en">
<head>
<meta charset="utf-8">
<title>Rosko Tamblin — Songwriter</title>
<link rel="stylesheet" href="https://fonts.googleapis.com/css2?family=Playfair+Display:wght@700;900&family=Roboto:wght@400;500;700&display=swap">
<style>
  :root {
    --black: #000000;
    --ink: #0d0d0d;
    --panel: #141414;
    --charcoal: #232323;
    --white: #ffffff;
    --soft: #d6d6d6;
    --muted: #bfbfbf;
    --orange: #f28a12;
    --arrow: #ff5a1f;
  }
  * { margin: 0; padding: 0; box-sizing: border-box; }
  html, body { width: 1200px; height: 3355px; overflow: hidden; }
  body {
    position: relative;
    background: var(--black);
    color: var(--white);
    font-family: "Roboto", Arial, sans-serif;
  }
  .abs { position: absolute; }
  .serif { font-family: "Playfair Display", Georgia, serif; font-weight: 900; text-transform: uppercase; }
  .rule { position: absolute; height: 3px; width: 52px; background: var(--orange); }
  .btn {
    position: absolute; display: flex; align-items: center; justify-content: center;
    border: 2px solid var(--orange); color: var(--orange);
    font-weight: 500; font-size: 16px; letter-spacing: .2px; text-transform: uppercase;
  }

  /* Header */
  .site-header { position: absolute; left: 0; top: 0; width: 1200px; height: 90px; z-index: 5; }
  .brand { position: absolute; left: 54px; top: 28px; font-family: "Playfair Display", Georgia, serif; font-weight: 700; font-size: 30px; }
  .main-nav a { position: absolute; top: 38px; font-size: 15px; color: var(--white); text-decoration: none; }
  .main-nav a.current { font-weight: 700; }

  /* Hero */
  .hero { position: absolute; left: 0; top: 0; width: 1200px; height: 716px;
    background: radial-gradient(ellipse at 25% 45%, #3a3a3a 0%, #161616 55%, #050505 100%); overflow: hidden; }
  .hero-photo { position: absolute; left: 560px; top: 80px; width: 640px; height: 636px;
    background: radial-gradient(ellipse at 55% 55%, #9a9a9a 0%, #4d4d4d 40%, #141414 75%, transparent 100%); }
  .hero-title { position: absolute; left: 110px; top: 272px; font-size: 51px; line-height: 52px; }
  .hero-lead { position: absolute; left: 110px; top: 396px; width: 380px; font-size: 16px; line-height: 22px; }

  /* Bio */
  .bio { position: absolute; left: 0; top: 716px; width: 1200px; height: 586px;
    background: radial-gradient(ellipse at 70% 70%, #3a3a3a 0%, #1c1c1c 45%, #0e0e0e 100%); overflow: hidden; }
  .bio-photo { position: absolute; left: 125px; top: 28px; width: 370px; height: 558px;
    background: radial-gradient(ellipse at 50% 45%, #d8d8d8 0%, #8a8a8a 45%, rgba(40,40,40,0) 75%); }
  .bio-title { position: absolute; left: 618px; top: 118px; font-size: 44px; }
  .bio-text { position: absolute; left: 619px; top: 206px; width: 510px; font-size: 15px; line-height: 27px; color: var(--soft); }

  /* Music */
  .music { position: absolute; left: 0; top: 1302px; width: 1200px; height: 551px; background: var(--black); }
  .section-title { position: absolute; left: 0; width: 1200px; text-align: center; font-size: 42px; }
  .album { position: absolute; top: 160px; width: 290px; }
  .album-cover { width: 290px; height: 215px; border-radius: 4px; }
  .album-name { margin-top: 40px; text-align: center; font-weight: 700; font-size: 17px; }
  .album-note { margin-top: 8px; text-align: center; font-size: 13px; line-height: 19px; color: var(--soft); }

  /* Discography */
  .discography { position: absolute; left: 0; top: 1853px; width: 1200px; height: 648px;
    background: linear-gradient(180deg, #2a2a2a 0%, #4a4a4a 30%, #1a1a1a 70%, #050505 100%); overflow: hidden; }
  .crowd { position: absolute; left: 0; top: 300px; width: 1200px; height: 348px;
    background: linear-gradient(180deg, rgba(0,0,0,0) 0%, rgba(0,0,0,.75) 40%, #000 100%); }
  .disco-text { position: absolute; left: 190px; top: 184px; width: 820px; text-align: center; font-size: 15px; line-height: 27px; color: var(--soft); }

  /* Blogs */
  .blogs { position: absolute; left: 0; top: 2501px; width: 1200px; height: 641px; background: var(--charcoal); }
  .post { position: absolute; top: 177px; width: 307px; height: 386px; background: var(--panel); }
  .post-image { width: 307px; height: 211px; }
  .post-title { position: absolute; left: 35px; top: 237px; font-weight: 700; font-size: 17px; text-transform: uppercase; }
  .post-text { position: absolute; left: 35px; top: 265px; width: 250px; font-size: 13px; line-height: 19px; color: var(--soft); }
  .post .btn { left: 38px; top: 322px; width: 118px; height: 34px; font-size: 11px; }

  /* Footer */
  .site-footer { position: absolute; left: 0; top: 3142px; width: 1200px; height: 213px; background: var(--black); }
  .foot-nav a { position: absolute; top: 48px; font-size: 15px; color: var(--white); text-decoration: none; }
  .copyright { position: absolute; left: 0; top: 88px; width: 1200px; text-align: center; font-size: 16px; color: var(--soft); }
  .social { position: absolute; top: 136px; width: 24px; height: 24px; border: 2px solid var(--white); border-radius: 50%; }
</style>
</head>
<body>

<section class="hero">
  <div class="hero-photo" role="img" aria-label="Black and white photo of the songwriter in a hat playing mandolin"></div>
  <h1 class="hero-title serif">Welcom to<br>Rosko Tamblin</h1>
  <p class="hero-lead">Sed ut perspiciatis unde omnis iste natus error sit voluptatem accusantium doloremque</p>
  <a class="btn" style="left:111px;top:459px;width:165px;height:49px;">Learn more</a>
</section>

<header class="site-header">
  <div class="brand">Rosko Tamblin</div>
  <nav class="main-nav">
    <a class="current" style="left:509px">ABOUT ME</a>
    <a style="left:658px">MY MUSIC</a>
    <a style="left:803px">BLOG</a>
    <a style="left:914px">GALLERY</a>
    <a style="left:1051px">CONTACT</a>
  </nav>
</header>

<section class="bio">
  <div class="bio-photo" role="img" aria-label="Portrait of the songwriter holding his hat"></div>
  <h2 class="bio-title serif">My Bio</h2>
  <div class="rule" style="left:620px;top:182px"></div>
  <p class="bio-text">Rosko Tamblin was born and raised in Houston, Texas. He began playing music at the age of eight when his sister returned home from summer camp and asked her parents to buy her a baritone ukulele. She taught her younger brother some chords on the ukulele and he was hooked. The following spring, they went to one of the border towns in Mexico and bought a Mexican guitar for $12. They restrung it with nylon strings and Tamblin began to learn how to play the guitar</p>
  <a class="btn" style="left:624px;top:419px;width:164px;height:49px;">Learn more</a>
</section>

<section class="music">
  <h2 class="section-title serif" style="top:52px">My Music</h2>
  <div class="rule" style="left:576px;top:111px"></div>
  <svg class="abs" style="left:70px;top:266px" width="18" height="26" viewBox="0 0 18 26"><path d="M14 3 L4 13 L14 23" fill="none" stroke="#fff" stroke-width="4"/></svg>
  <svg class="abs" style="left:1124px;top:266px" width="18" height="26" viewBox="0 0 18 26"><path d="M4 3 L14 13 L4 23" fill="none" stroke="var(--arrow)" stroke-width="4"/></svg>
  <div class="album" style="left:125px">
    <div class="album-cover" role="img" aria-label="Colourful CD cover with disc" style="background:linear-gradient(120deg,#e8456b,#7a4ec9 45%,#37c3d6 70%,#d9d9d9)"></div>
    <div class="album-name">Sed ut perspiciatis</div>
    <div class="album-note">omnis iste natus error sit voluptatem<br>accusantium doloremque</div>
  </div>
  <div class="album" style="left:467px">
    <div class="album-cover" role="img" aria-label="Stormy CD cover with disc" style="background:linear-gradient(120deg,#5a6a9a,#2a2a3a 45%,#b0582a 65%,#cfcfcf)"></div>
    <div class="album-name">Sed ut perspiciatis</div>
    <div class="album-note">omnis iste natus error sit voluptatem<br>accusantium doloremque</div>
  </div>
  <div class="album" style="left:810px">
    <div class="album-cover" role="img" aria-label="Warm toned CD cover with disc" style="background:linear-gradient(120deg,#f0a020,#d8662a 40%,#e8d3b5 70%,#d9d9d9)"></div>
    <div class="album-name">Sed ut perspiciatis</div>
    <div class="album-note">omnis iste natus error sit voluptatem<br>accusantium doloremque</div>
  </div>
</section>

<section class="discography">
  <div class="crowd" role="img" aria-label="Concert crowd with raised hands"></div>
  <h2 class="section-title serif" style="top:96px">Discography</h2>
  <div class="rule" style="left:578px;top:161px"></div>
  <p class="disco-text">Tamblin stopped listening to or playing music from the late 80s into the mid-nineties, when the singer songwriter movement began.Intrigued by the sound of these artists, he began to write again. In the past he played almost exclusively electric guitar but during this phase he moved into acoustic guitar and mandolin</p>
  <a class="btn" style="left:525px;top:281px;width:164px;height:49px;">Learn more</a>
</section>

<section class="blogs">
  <h2 class="section-title serif" style="top:68px;left:-10px">Latest Blogs</h2>
  <div class="rule" style="left:564px;top:126px"></div>
  <article class="post" style="left:113px">
    <div class="post-image" role="img" aria-label="Black and white photo of a mandolin player" style="background:linear-gradient(135deg,#d0d0d0,#3a3a3a 60%,#111)"></div>
    <h3 class="post-title">Avoluptatem accusantium</h3>
    <p class="post-text">omnis iste natus error sit voluptatem accusantium doloremque</p>
    <a class="btn">Learn more</a>
  </article>
  <article class="post" style="left:442px">
    <div class="post-image" role="img" aria-label="Guitarist on stage under blue light" style="background:linear-gradient(135deg,#7a1a2a,#1a2a9a 55%,#0a0a4a)"></div>
    <h3 class="post-title">Labore et dolore</h3>
    <p class="post-text">omnis iste natus error sit voluptatem accusantium doloremque</p>
    <a class="btn">Learn more</a>
  </article>
  <article class="post" style="left:772px">
    <div class="post-image" role="img" aria-label="Glowing music notes over hands" style="background:linear-gradient(135deg,#1a3a6a,#3a5a8a 45%,#c08a3a 75%,#10203a)"></div>
    <h3 class="post-title">Nihil molestiaeum</h3>
    <p class="post-text">omnis iste natus error sit voluptatem accusantium doloremque</p>
    <a class="btn">Learn more</a>
  </article>
</section>

<footer class="site-footer">
  <nav class="foot-nav">
    <a style="left:275px">HOME</a>
    <a style="left:372px">ABOUT ME</a>
    <a style="left:501px">MY MUSIC</a>
    <a style="left:628px">BLOG</a>
    <a style="left:720px">GALLERY</a>
    <a style="left:837px">CONTACT</a>
  </nav>
  <p class="copyright">© 2019-2020 Rosko Tamblin</p>
  <span class="social" style="left:526px" aria-label="Social link"></span>
  <span class="social" style="left:571px" aria-label="Social link"></span>
  <span class="social" style="left:619px" aria-label="Social link"></span>
</footer>

</body>
</html>
```